Finding the Root: Reason in Clinical Choice-Crafting

I'd like a cover that looks like it would fit on the shelf next to "The Illness Mirage" by Corwin Talley, "The Close of Forgetting" by Hugh Marchetti, "Meal Mend" by Paul Grieve, "The Energy Restart Plan" by Oscar Pemberley or "The Gland Restart Plan" by the same or "The Cortex Restart Plan" by the same ... either text only (with some interesting fonts that make the title stand out, and the subtitle smaller) or a relevant image, though I'm not entirely sure what that would be since this is a book about big-picture medical decision making.
Author name is Dr Tessa Morrow, NMD
I'll eventually request an e-book, paperback, and audio cover from the winner...

Target Market(s)

practicing physicians

Industry/Entity Type

medicine

Requirements
Must have
• look similar to other books in the genre

```html
<!DOCTYPE html>
<html lang="en">
<head>
<meta charset="UTF-8">
<title>Finding the Root — Book Cover</title>
<link rel="stylesheet" href="https://fonts.googleapis.com/css2?family=Source+Serif+4:ital,opsz,wght@0,8..60,400;0,8..60,500;1,8..60,400;1,8..60,500&family=Montserrat:wght@400;500;600&display=swap">
<style>
  :root {
    --backdrop: #959595;
    --paper: #ffffff;
    --navy: #13294f;
    --leaf: #4b7d45;
    --rule: #a3a8b5;
    --serif: "Source Serif 4", Georgia, serif;
    --sans: "Montserrat", Arial, sans-serif;
  }
  * { margin: 0; padding: 0; box-sizing: border-box; }
  html, body {
    width: 1200px; height: 1200px; overflow: hidden;
    background: var(--backdrop);
  }
  .cover {
    position: absolute;
    left: 248px; top: 73px;
    width: 703px; height: 1054px;
    background: var(--paper);
  }
  .endorsement {
    position: absolute; top: 32px; left: 0; width: 100%;
    text-align: center;
    font-family: var(--sans); font-size: 14px; line-height: 21px;
    color: #2a2a2a;
  }
  .endorsement .source {
    display: block; margin-top: 4px;
    color: var(--leaf); font-weight: 600; letter-spacing: 0.08em;
  }
  .title { font-family: var(--serif); color: var(--navy); font-weight: 500; }
  .title-first {
    position: absolute; left: 100px; top: 130px;
    font-size: 150px; line-height: 1; font-weight: 500;
    letter-spacing: -0.01em;
  }
  .title-second {
    position: absolute; left: 94px; top: 272px;
    display: flex; align-items: baseline; gap: 14px;
    line-height: 1;
  }
  .title-joiner { font-size: 74px; font-style: italic; font-weight: 400; color: var(--navy); }
  .title-key { font-size: 210px; font-weight: 500; color: var(--leaf); letter-spacing: -0.015em; }
  .rule { position: absolute; height: 1px; background: var(--rule); }
  .rule-sub-top { left: 173px; width: 335px; top: 497px; }
  .rule-sub-bottom { left: 173px; width: 356px; top: 667px; }
  .subtitle {
    position: absolute; left: 0; width: 100%; top: 518px;
    text-align: center; color: var(--navy);
    font-family: var(--sans); font-weight: 500;
    font-size: 30px; line-height: 45px; letter-spacing: 0.16em;
  }
  .subtitle .accent {
    display: block; font-family: var(--serif); color: var(--leaf);
    font-weight: 400; font-size: 33px; letter-spacing: 0.14em;
  }
  .emblem {
    position: absolute; left: 272px; top: 690px;
    width: 160px; height: 226px; border-radius: 50% 50% 42% 42%;
    background: radial-gradient(circle at 50% 32%, #8fbf82 0%, #5c8d55 45%, #2c4a62 80%, #1b3157 100%);
    opacity: 0.9;
  }
  .promise {
    position: absolute; top: 768px;
    font-family: var(--sans); font-weight: 600; font-size: 13px;
    line-height: 31px; letter-spacing: 0.14em; color: var(--leaf);
    text-align: center; width: 190px;
  }
  .promise-left { left: 72px; }
  .promise-right { left: 436px; }
  .rule-author-top { left: 98px; width: 506px; top: 946px; }
  .rule-author-bottom { left: 98px; width: 506px; top: 1011px; }
  .author {
    position: absolute; left: 0; width: 100%; top: 960px;
    text-align: center; font-family: var(--sans); font-weight: 600;
    font-size: 26px; line-height: 38px; letter-spacing: 0.3em;
    color: var(--leaf);
  }
</style>
</head>
<body>
  <main class="cover">
    <p class="endorsement">
      “A must-read for anyone ready to take charge of their health<br>
      and work with their doctor to get to the root cause.”
      <span class="source">—PAUL GRIEVE, MD</span>
    </p>

    <h1 class="title">
      <span class="title-first">Finding</span>
      <span class="title-second">
        <span class="title-joiner">the</span>
        <span class="title-key">Root</span>
      </span>
    </h1>

    <div class="rule rule-sub-top"></div>
    <h2 class="subtitle">
      REASON IN
      <span class="accent">CLINICAL</span>
      CHOICE-CRAFTING
    </h2>
    <div class="rule rule-sub-bottom"></div>

    <p class="promise promise-left">BETTER QUESTIONS<br>BETTER ANSWERS</p>
    <div class="emblem" role="img" aria-label="Illustration of a leafy green tree with spreading navy roots"></div>
    <p class="promise promise-right">BETTER DECISIONS<br>BETTER HEALTH</p>

    <div class="rule rule-author-top"></div>
    <p class="author">DR TESSA MORROW, NMD</p>
    <div class="rule rule-author-bottom"></div>
  </main>
</body>
</html>
```